Lune Tavi Wigs " Styling Foam"

I need a label created for my product . The bottle size is 50ml so it must be designed to fit that size bottle. I will post my logo and examples of my bottle size. I want the label design to be simple and cute. ill also add pictures of my website, so you can get ideas from there. The bottle is white so I want the main colors to be white and pink. All colors on the label must match my logo. I love glitter as well.

I know for sure I want my logo big, and I want "Styling Foam'',
then under styling foam I would like " Medium Hold" in a different front. be very creative.

Then under that I would like it to say " No Alcohol , Saulfate or Paraben

please make sure on the label in the front it has "NET: 7.0 oz / 200g" so people know what size it is.

I would like a glitter border on the label.

I also want the back of the label to have directions.

And ingredients list too . Very small not too big at all.

Target Market(s)

My target market is woman of all ages .. but mainly woman from ages 26-65

Industry/Entity Type

Hair And Beauty

Font styles to use
Serif
Sans Serif
Decorative
Script

Colors
e667a6
eda3c7
f9d9e8
e34297

Requirements
Must have
• The project must match the colors of my logo, it must have a nice pretty glitter border . It must be simple and clean . But still stylish ! I don’t want everything after my logo to be in the same font . Have fun with this design, be creative. My logo and “ Styling Foam” must be the two centerpiece!
Nice to have
• It will be nice to have different fonts! And nice to have all the colors that match my logo
Must be expensive looking !!
Very eye catching!
Should not have
• Do not add colors that my logo doesn’t have !!!!
I don’t want it to look too plain and boring ! I want it to be classy and expensive looking !

```html
<!DOCTYPE html>
<html lang="en">
<head>
<meta charset="utf-8">
<title>Lune Tavi Wigs – Styling Foam Labels</title>
<link rel="stylesheet" href="https://fonts.googleapis.com/css2?family=Oswald:wght@500;700&family=Rubik+Dirt&family=Kaushan+Script&family=Roboto:wght@400;700&display=swap">
<style>
  :root {
    --backdrop: #6a7ea6;
    --white: #ffffff;
    --pink: #e34297;
    --pink-soft: #e667a6;
    --pink-light: #eda3c7;
    --pink-pale: #f9d9e8;
    --magenta: #c21fd0;
    --ink: #2b2b2b;
    --black: #0b0b0b;
  }
  * { box-sizing: border-box; margin: 0; padding: 0; }
  html, body { width: 1200px; height: 975px; overflow: hidden; }
  body { background: var(--backdrop); position: relative; font-family: "Roboto", sans-serif; }

  .label {
    position: absolute;
    top: 330px;
    width: 200px;
    height: 530px;
    overflow: hidden;
  }
  .label--light { left: 342px; background: var(--white); }
  .label--dark { left: 655px; background: var(--black); }

  .brand {
    position: absolute;
    left: 0; right: 0;
    top: 72px;
    text-align: center;
    font-family: "Oswald", sans-serif;
    font-weight: 500;
    font-size: 22px;
    letter-spacing: 1px;
    line-height: 1.1;
  }
  .label--light .brand { color: var(--pink); }
  .label--dark .brand { color: var(--white); }

  /* Light label */
  .label--light .title {
    position: absolute;
    right: 4px;
    top: 148px;
    text-align: right;
    font-family: "Rubik Dirt", sans-serif;
    font-size: 40px;
    line-height: 1.05;
    color: var(--pink);
  }
  .label--light .band {
    position: absolute;
    left: 0; right: 0;
    top: 235px;
    bottom: 0;
    background: var(--pink);
  }
  .hold-block {
    position: absolute;
    right: 10px;
    top: 270px;
    text-align: right;
    font-family: "Oswald", sans-serif;
    font-weight: 700;
    font-size: 44px;
    line-height: 1.02;
    color: var(--ink);
  }
  .hold-rule {
    position: absolute;
    left: 28px; right: 10px;
    top: 395px;
    height: 2px;
    background: var(--ink);
  }
  .claims {
    position: absolute;
    right: 10px;
    top: 405px;
    text-align: right;
    font-size: 15px;
    line-height: 1.3;
    color: var(--ink);
  }
  .net {
    position: absolute;
    font-size: 11px;
    font-weight: 700;
    white-space: nowrap;
  }
  .label--light .net {
    right: 8px;
    top: 450px;
    padding: 2px 8px;
    border: 1.5px solid var(--ink);
    border-radius: 10px;
    background: var(--white);
    color: var(--black);
  }

  /* Dark label */
  .burst {
    position: absolute;
    left: 0; right: 0;
    top: 150px;
    height: 210px;
    background: radial-gradient(circle at 50% 50%, var(--black) 0 24%, #8e1aa0 34%, var(--magenta) 48%, #6a1078 62%, var(--black) 74%);
  }
  .label--dark .title {
    position: absolute;
    left: 0; right: 0;
    top: 205px;
    text-align: center;
    font-family: "Oswald", sans-serif;
    font-weight: 700;
    color: var(--white);
    line-height: 1.05;
  }
  .title__line1 { font-size: 30px; display: block; }
  .title__line2 { font-size: 44px; display: block; }
  .hold-script {
    position: absolute;
    left: 0; right: 0;
    top: 380px;
    text-align: center;
    font-family: "Kaushan Script", cursive;
    font-size: 30px;
    color: var(--white);
  }
  .free-icons {
    position: absolute;
    left: 0; right: 0;
    top: 430px;
    display: flex;
    justify-content: center;
    gap: 8px;
  }
  .label--dark .net {
    left: 0; right: 0;
    top: 472px;
    text-align: center;
    color: var(--white);
  }
</style>
</head>
<body>

  <section class="label label--light">
    <div class="brand">Lune Tavi<br>Wigs</div>
    <div class="title">STYLING<br>FOAM</div>
    <div class="band"></div>
    <div class="hold-block">MEDIUM<br>HOLD</div>
    <div class="hold-rule"></div>
    <div class="claims">No Alcohol<br>Saulfate/Paraben</div>
    <div class="net">NET: 7.0 oz / 200g</div>
  </section>

  <section class="label label--dark">
    <div class="brand">Lune Tavi<br>Wigs</div>
    <div class="burst" role="img" aria-label="Radiating magenta dot pattern behind the product name"></div>
    <div class="title">
      <span class="title__line1">STYLING</span>
      <span class="title__line2">FOAM</span>
    </div>
    <div class="hold-script">Medium Hold</div>
    <div class="free-icons">
      <svg width="26" height="26" viewBox="0 0 26 26" aria-label="Alcohol free">
        <circle cx="13" cy="13" r="12" fill="var(--pink)"/>
        <rect x="9" y="9" width="5" height="10" rx="1" fill="none" stroke="#fff" stroke-width="1.5"/>
        <line x1="6" y1="6" x2="20" y2="20" stroke="#fff" stroke-width="1.8"/>
      </svg>
      <svg width="26" height="26" viewBox="0 0 26 26" aria-label="Paraben free">
        <circle cx="13" cy="13" r="12" fill="var(--pink)"/>
        <path d="M11 7 h4 M12 7 v5 l-4 7 h10 l-4 -7 v-5" fill="none" stroke="#fff" stroke-width="1.5"/>
        <line x1="6" y1="6" x2="20" y2="20" stroke="#fff" stroke-width="1.8"/>
      </svg>
    </div>
    <div class="net">NET: 7.0 oz / 200g</div>
  </section>

</body>
</html>
```